Coffeeshop menu for filter tip

We want to have a cannabis (coffeeshop) menu in the size 25mm wide x 60mm wide. Some examples attached.

it must have the following text:
Menu

WEED p/g
Oblivane €16
Cloudplum €14
Tide Runner €14
Quincefig €16
Mega Marsh €14
Grey Heron €14

HASH p/g
Tashar Amber €12
Pebble Frost€11
Lime Dunes €14
Ash Petal €10

Target Market(s)

tourist in Amsterdam

Requirements
Nice to have
• cannabis sign leaf
• No Cigarettes allowed symbol

```html
<!DOCTYPE html>
<html lang="en">
<head>
<meta charset="utf-8">
<title>Coffeeshop Menu</title>
<link rel="stylesheet" href="https://fonts.googleapis.com/css2?family=Neucha&family=Patrick+Hand&display=swap">
<style>
  :root {
    --paper: #bfb6a9;
    --leaf: #a9b98a;
    --heading: #173f47;
    --ink: #2c2030;
    --shadow: rgba(60, 50, 45, 0.35);
    --sign-red: #cc6a52;
    --sign-fill: #ebe6dd;
    --sign-dark: #3a3a3a;
  }
  * { margin: 0; padding: 0; box-sizing: border-box; }
  html, body {
    width: 1200px;
    height: 2880px;
    overflow: hidden;
    background: var(--paper);
  }
  .menu-card {
    position: relative;
    width: 1200px;
    height: 2880px;
    background: var(--paper);
    overflow: hidden;
  }
  .leaf-backdrop {
    position: absolute;
    inset: 0;
    background:
      radial-gradient(ellipse 720px 1500px at 560px 2300px, var(--leaf) 0%, var(--leaf) 45%, rgba(169, 185, 138, 0) 100%);
  }
  .menu-title {
    position: absolute;
    left: 78px;
    top: 110px;
    font-family: "Patrick Hand", cursive;
    font-weight: 400;
    font-size: 380px;
    line-height: 1;
    color: var(--heading);
    text-shadow: 4px 5px 3px var(--shadow);
  }
  .section {
    position: absolute;
    left: 80px;
    width: 1043px;
  }
  .section--weed { top: 545px; }
  .section--hash { top: 1770px; }
  .section-head {
    position: relative;
    height: 250px;
  }
  .section-title {
    position: absolute;
    left: 0;
    top: 0;
    font-family: "Patrick Hand", cursive;
    font-weight: 400;
    font-size: 230px;
    line-height: 1;
    color: var(--heading);
    text-shadow: 4px 5px 3px var(--shadow);
  }
  .unit {
    position: absolute;
    right: 0;
    bottom: 0;
    font-family: "Neucha", cursive;
    font-size: 120px;
    line-height: 1;
    color: var(--ink);
    text-shadow: 3px 4px 3px var(--shadow);
  }
  .price-list { list-style: none; }
  .price-row {
    display: flex;
    align-items: baseline;
    height: 125px;
    font-family: "Neucha", cursive;
    font-size: 120px;
    line-height: 125px;
    color: var(--ink);
    text-shadow: 3px 4px 3px var(--shadow);
  }
  .item-name { white-space: nowrap; }
  .leader {
    flex: 1;
    margin: 0 4px;
    border-bottom: 7px dotted var(--ink);
  }
  .item-price { white-space: nowrap; }
  .no-smoking {
    position: absolute;
    left: 950px;
    top: 2630px;
    width: 212px;
    height: 212px;
  }
</style>
</head>
<body>
<main class="menu-card">
  <div class="leaf-backdrop" role="img" aria-label="Large soft green cannabis leaf in the background"></div>

  <h1 class="menu-title">Menu</h1>

  <section class="section section--weed">
    <div class="section-head">
      <h2 class="section-title">Weed</h2>
      <span class="unit">p/g</span>
    </div>
    <ul class="price-list">
      <li class="price-row"><span class="item-name">Oblivane</span><span class="leader"></span><span class="item-price">€16</span></li>
      <li class="price-row"><span class="item-name">Cloudplum</span><span class="leader"></span><span class="item-price">€14</span></li>
      <li class="price-row"><span class="item-name">Tide Runner</span><span class="leader"></span><span class="item-price">€14</span></li>
      <li class="price-row"><span class="item-name">Quincefig</span><span class="leader"></span><span class="item-price">€16</span></li>
      <li class="price-row"><span class="item-name">Mega Marsh</span><span class="leader"></span><span class="item-price">€14</span></li>
      <li class="price-row"><span class="item-name">Grey Heron</span><span class="leader"></span><span class="item-price">€14</span></li>
    </ul>
  </section>

  <section class="section section--hash">
    <div class="section-head">
      <h2 class="section-title">Hash</h2>
      <span class="unit">p/g</span>
    </div>
    <ul class="price-list">
      <li class="price-row"><span class="item-name">Tashar Amber</span><span class="leader"></span><span class="item-price">€12</span></li>
      <li class="price-row"><span class="item-name">Pebble Frost</span><span class="leader"></span><span class="item-price">€11</span></li>
      <li class="price-row"><span class="item-name">Lime Dunes</span><span class="leader"></span><span class="item-price">€14</span></li>
      <li class="price-row"><span class="item-name">Ash Petal</span><span class="leader"></span><span class="item-price">€10</span></li>
    </ul>
  </section>

  <svg class="no-smoking" viewBox="0 0 212 212" role="img" aria-label="No smoking sign">
    <circle cx="106" cy="106" r="96" fill="var(--sign-fill)" stroke="var(--sign-red)" stroke-width="16"/>
    <rect x="40" y="112" width="108" height="18" fill="var(--sign-dark)"/>
    <rect x="150" y="112" width="22" height="18" fill="var(--sign-dark)"/>
    <path d="M132 98 C132 80 160 80 160 62 C160 48 146 44 146 34" fill="none" stroke="var(--sign-dark)" stroke-width="7" stroke-linecap="round"/>
    <line x1="42" y1="42" x2="170" y2="170" stroke="var(--sign-red)" stroke-width="16"/>
  </svg>
</main>
</body>
</html>
```